Maple Roster Business Card for recruitment company

We are looking for a Business Card Design that incorporates our personal details and our busines name and logo. We are a specialized search consultancy that recruit Property and Construction professionals.
We would like a business card that stands out and is appealing to the Construction and Property industry as well.

Target Market(s)

people in the construction and property industry

Contact Information for Business Card

Business Name and logo

Font styles to use
Serif

Colors
0094D4
00A9DD
6FCCEA
C7EBF8
E9F6FB

Requirements
Must have
• Business name and logo as well as contact details
Should not have
• No photos of us please

```html
<!DOCTYPE html>
<html lang="en">
<head>
<meta charset="utf-8">
<title>Maple Roster Business Card</title>
<link href="https://fonts.googleapis.com/css2?family=Montserrat:wght@300;400;600&display=swap" rel="stylesheet">
<style>
  :root {
    --page-bg: #1c1d1f;
    --card-teal: #053f52;
    --card-white: #ffffff;
    --curve-shadow: #9a9da0;
    --ink-light: #ffffff;
  }
  * { margin: 0; padding: 0; box-sizing: border-box; }
  html, body {
    width: 1200px; height: 900px; overflow: hidden;
    background: var(--page-bg);
    font-family: "Montserrat", Arial, sans-serif;
  }
  .stage {
    position: relative; width: 1200px; height: 900px;
    display: flex; flex-direction: column; align-items: center; justify-content: center; gap: 56px;
  }
  .card {
    position: relative; width: 600px; height: 343px;
    border-radius: 22px; overflow: hidden;
    background: var(--card-teal);
    box-shadow: 0 10px 28px rgba(0,0,0,0.5);
  }
  .card-art { position: absolute; inset: 0; width: 100%; height: 100%; }
  .brand-name {
    position: absolute; font-weight: 300; text-transform: uppercase;
    letter-spacing: 0.06em; white-space: nowrap;
  }
  .card-front .brand-name {
    left: 262px; top: 112px; font-size: 34px; color: var(--card-teal);
  }
  .contact-list {
    position: absolute; left: 30px; top: 176px; list-style: none;
    color: var(--ink-light); font-size: 13px; line-height: 20px; font-weight: 400;
  }
  .contact-list li { display: flex; align-items: center; gap: 8px; }
  .contact-list svg { width: 11px; height: 11px; flex: none; }
  .holder {
    position: absolute; right: 160px; top: 282px; text-align: right; color: var(--ink-light);
  }
  .holder-name { font-size: 19px; font-weight: 600; letter-spacing: 0.05em; text-transform: uppercase; }
  .holder-role { font-size: 13px; font-weight: 300; letter-spacing: 0.08em; text-transform: uppercase; }
  .card-back { display: flex; align-items: center; justify-content: center; }
  .card-back .brand-name { position: static; font-size: 42px; color: var(--ink-light); }
</style>
</head>
<body>
<main class="stage">
  <section class="card card-front" aria-label="Business card front">
    <svg class="card-art" viewBox="0 0 600 343" aria-hidden="true">
      <path d="M166,0 Q224,222 600,236 L600,262 Q214,252 158,0 Z" fill="var(--card-teal)"/>
      <path d="M178,0 Q236,226 600,240 L600,236 Q232,216 174,0 Z" fill="var(--curve-shadow)"/>
      <path d="M174,0 Q232,216 600,232 L600,0 Z" fill="var(--card-white)"/>
      <path d="M156,0 Q212,256 600,266" fill="none" stroke="var(--card-white)" stroke-width="3"/>
    </svg>
    <div class="brand-name">Maple Roster</div>
    <ul class="contact-list">
      <li><svg viewBox="0 0 12 12"><path d="M3,1 L5,3.5 L4,5 Q5,7 7,8 L8.5,7 L11,9 L9.5,11 Q4,10.5 1,3 Z" fill="#fff"/></svg>+64 21 480 2271</li>
      <li><svg viewBox="0 0 12 12"><rect x="1" y="2.5" width="10" height="7" fill="none" stroke="#fff"/><path d="M1,2.5 L6,6.5 L11,2.5" fill="none" stroke="#fff"/></svg>anna@mapleroster.nz</li>
      <li><svg viewBox="0 0 12 12"><circle cx="6" cy="6" r="5" fill="none" stroke="#fff"/><path d="M1,6 H11 M6,1 Q3,6 6,11 M6,1 Q9,6 6,11" fill="none" stroke="#fff" stroke-width="0.8"/></svg>www.mapleroster.nz</li>
      <li><svg viewBox="0 0 12 12"><path d="M6,11 Q2,6 2,4.5 A4,4 0 0 1 10,4.5 Q10,6 6,11 Z" fill="#fff"/><circle cx="6" cy="4.5" r="1.4" fill="var(--card-teal)"/></svg>Harbourview, New Zealand</li>
    </ul>
    <div class="holder">
      <div class="holder-name">Daniel Hartley</div>
      <div class="holder-role">Founder</div>
    </div>
  </section>

  <section class="card card-back" aria-label="Business card back">
    <div class="brand-name">Maple Roster</div>
  </section>
</main>
</body>
</html>
```